I need a business card design for a new dance business. I offer classical Indian dance tuition and also professional performances. I want to offer the community a variety of Indian dance experiences which include: group class and private tuition, school and preschool educational courses and workshops. dance theatre performances, community function workshops and performances, Kids Bollywood parties, wedding & conference performances, mouth percussion classes, Indian mythology/ dance costume and make up workshops.
The final design should communicate a feeling and impression of the vibrance and energy of Indian dance.
Updates
Hi Everyone,
Project Deadline Extended
Reason: I would like to refine a few changes to the details of this lovely design and we have run out of time!
Project Deadline Extended
Reason: Still waiting to hear back form designer re two possible changes to the card design. Tomorrow is the deadline and I have sent several messages but with no response. I need to see this through before selecting this lovely design.
Thank you.
Tara
Industry/Entity Type
Preschool
Requirements
Must have
- The front of the business card should have the photo of me (my face and torso), surrounded entirely by a border of bright magenta (to match the magenta of my lipstick - it is the same as the magenta on my skirt in the second photo). Within the top border I want (perhaps yellow-gold) writing to say "Tara Holloway - Artistic Director" and within the bottom border it should read "Saffron Lantern Indian Dance." If you turn the card on its side the left border should have my telephone number: 0417 862 493 and the right-hand border should read: saffronlanternindiandance@quillmail.example
The reverse of the card should be the orange of the dance costume
and I'd like the picture of my feet and legs to be on the right side of the back of the card as a side border. Centre-aligned on the orange background it should read (perhaps in dark magenta):
Indian dance classes + private tuition
School + preschool educational courses and workshops
Dance theatre performances
Community function workshops and performances
Children's Bollywood parties
Wedding + conference performances
Mouth percussion classes
Indian mythology and dance demonstration workshops
Dance costume and make-up workshops
Nice to have
- A lovely artistic but easy-to-read font would be nice.

```html
<!DOCTYPE html>
<html lang="en">
<head>
<meta charset="utf-8">
<title>Saffron Lantern Indian Dance – Business Card</title>
<link href="https://fonts.googleapis.com/css2?family=Lobster+Two:wght@400&family=Andika&family=Varela+Round&display=swap" rel="stylesheet">
<style>
  :root {
    --saffron: #dc7a32;
    --violet: #652d8f;
    --magenta: #a1195f;
    --gold: #e5a23a;
    --white: #ffffff;
    --paper: #ffffff;
  }
  * { margin: 0; padding: 0; box-sizing: border-box; }
  html, body { width: 1200px; height: 900px; overflow: hidden; background: var(--paper); }
  .canvas { position: relative; width: 1200px; height: 900px; }

  .card { position: absolute; top: 42px; width: 481px; height: 787px; overflow: hidden; }
  .card--front { left: 101px; background: var(--saffron); }
  .card--back { left: 616px; background: var(--violet); }

  .front__photo {
    position: absolute; left: 120px; top: 0; width: 361px; height: 703px;
    background:
      radial-gradient(ellipse at 60% 55%, rgba(229,162,58,.85) 0%, rgba(229,162,58,0) 40%),
      linear-gradient(160deg, #5a1a3c 0%, #b01f70 35%, #c9306f 55%, #e3a04a 80%, var(--saffron) 100%);
    -webkit-mask-image: linear-gradient(90deg, transparent 0%, #000 18%);
            mask-image: linear-gradient(90deg, transparent 0%, #000 18%);
  }
  .front__title {
    position: absolute; left: 0; width: 230px; top: 354px;
    font-family: "Lobster Two", cursive; font-weight: 400; font-style: normal;
    font-size: 44px; line-height: 59px; color: var(--violet); text-align: center;
  }
  .front__name {
    position: absolute; left: 10px; top: 618px;
    font-family: "Andika", sans-serif; font-weight: 400; font-size: 34px;
    line-height: 40px; color: var(--white); letter-spacing: 0.5px;
  }
  .front__phone-band {
    position: absolute; left: 0; bottom: 0; width: 100%; height: 84px;
    background: var(--violet);
    display: flex; align-items: center; justify-content: center;
  }
  .front__phone {
    font-family: "Varela Round", sans-serif; font-size: 52px;
    color: var(--saffron); letter-spacing: 1px;
  }

  .back__contact-band {
    position: absolute; top: 0; left: 0; width: 100%; height: 88px;
    background: var(--saffron); padding: 11px 20px 0 0; text-align: right;
    font-family: "Andika", sans-serif; font-size: 30px; line-height: 33px;
    color: var(--violet); letter-spacing: 1px;
  }
  .back__services {
    position: absolute; top: 143px; left: 0; width: 100%; list-style: none;
    text-align: center; font-family: "Andika", sans-serif;
    font-size: 30px; line-height: 65px; color: var(--white); letter-spacing: 0.6px;
  }
  .back__photo {
    position: absolute; left: 34px; top: 512px; width: 416px; height: 275px;
    background: radial-gradient(ellipse at 50% 60%, #e9b04a 0%, #d8953a 35%, #8a2146 65%, rgba(101,45,143,0) 72%);
  }
</style>
</head>
<body>
<div class="canvas">
  <section class="card card--front">
    <div class="front__photo" role="img" aria-label="Photo of a dancer's foot and legs in a magenta and gold silk costume with ankle bells"></div>
    <h1 class="front__title">Saffron<br>Lantern<br>Indian<br>Dance</h1>
    <p class="front__name">Tara Holloway</p>
    <div class="front__phone-band"><p class="front__phone">0417 862 493</p></div>
  </section>

  <section class="card card--back">
    <div class="back__contact-band">
      <p>dance@taraholloway.example</p>
      <p>www.taraholloway.example</p>
    </div>
    <ul class="back__services">
      <li>group + individual classes</li>
      <li>school + preschool workshops</li>
      <li>dance theatre performances</li>
      <li>community + private functions</li>
      <li>mouth percussion tuition</li>
    </ul>
    <div class="back__photo" role="img" aria-label="Photo of the dancer in gold costume and jewellery posing with raised hands"></div>
  </section>
</div>
</body>
</html>
```